Halvik - consultancy website

I need a new design for my webpage/presence [to be functioning with Wordpress - I have a programmer to set it up but not the design idea].
My company is Halvik - a consultancy firm focused on growth management for Swedish SME's primarily;. We call it Leadership toolkit for firms on the rise, kind of a doctor helping small become big. Contentwise, its a simple frontpage + 3-4 subpages with content re company/myself/focus etc. The new site should communicate a fresh, trustworthy take yet simple and functional on all devices [i.e. think UI compatible for mobile/tablet]. Current building parts/form elements are
a) existing logo and text elements
b) existing pictures
c) the yellowish color
colours and new ideas on pictures/positioning are welcome. I prefer a 'full width page' solution with centralised text elements but that's all up to you to suggest. Current site is a quickfix made by myself - now I'm moving it to a new platform so want to take the opportunity to make it
Nothing superspecial as it is a 2-man show; on the other hand I still want to have a modern & fresh reflection of my brand in digital environments. Help me out!
www.halvik-demo.se
Best
Lina Bergqvist

```html
<!DOCTYPE html>
<html lang="en">
<head>
<meta charset="utf-8">
<title>Halvik – Services</title>
<link href="https://fonts.googleapis.com/css2?family=PT+Serif&family=Arimo:wght@400;700&display=swap" rel="stylesheet">
<style>
:root{
  --gold:#c47f27;
  --orange:#eda03a;
  --ink:#1f1f1f;
  --card-title:#26303b;
  --body:#6d6d6d;
  --line:#e6e6e6;
  --crumb-bg:#f5f5f5;
  --cta-bg:#333333;
  --footer-bg:#1c1c1c;
  --bottom-bg:#0d0d0d;
  --fb:#3b5a9a;
  --tw:#43a9e0;
  --gp:#dd4b39;
}
*{margin:0;padding:0;box-sizing:border-box}
html,body{width:715px;height:1200px;overflow:hidden;background:#fff}
body{position:relative;font-family:"Arimo",Arial,sans-serif;color:var(--ink)}
.abs{position:absolute}

/* header */
.site-header{position:absolute;left:0;top:0;width:715px;height:79px;background:#fff}
.brand-name{left:58px;top:14px;font-family:"PT Serif",Georgia,serif;font-size:31px;line-height:1;color:var(--ink)}
.brand-tagline{left:60px;top:47px;font-family:"PT Serif",Georgia,serif;font-size:8.6px;color:var(--ink)}
.main-nav a{position:absolute;top:36px;font-size:8.8px;color:var(--ink);text-decoration:none}
.main-nav a.active{color:var(--gold)}
.nav-underline{left:482px;top:52px;width:64px;height:1px;background:var(--gold)}

/* breadcrumb */
.breadcrumb{left:0;top:79px;width:715px;height:33px;background:var(--crumb-bg);font-size:8.6px;color:#555;padding:12px 0 0 58px}
.breadcrumb .sep{margin:0 4px}
.breadcrumb .current{color:var(--gold)}

/* intro */
.section-title{left:0;width:715px;top:150px;text-align:center;font-size:15.5px;font-weight:700}
.section-intro{left:58px;width:598px;top:182px;text-align:center;font-size:8.4px;line-height:12.4px;color:#555}

/* service cards */
.service-card{position:absolute;left:58px;width:598px;height:134px;border:1px solid var(--line);background:#fff}
.service-icon{position:absolute;left:17px;top:27px;width:84px;height:84px;border-radius:50%;background:var(--gold)}
.service-icon svg{position:absolute;left:22px;top:22px;width:40px;height:40px}
.service-title{position:absolute;left:118px;top:26px;font-size:10.4px;font-weight:700;color:var(--card-title)}
.service-text{position:absolute;left:118px;top:42px;width:462px;font-size:6.5px;line-height:11.2px;color:var(--body)}

/* call to action */
.cta{left:0;top:866px;width:715px;height:168px;background:var(--cta-bg);text-align:center;color:#fff}
.cta-heading{position:absolute;left:0;width:715px;top:45px;font-size:19px;font-weight:700;letter-spacing:2.2px}
.cta-sub{position:absolute;left:0;width:715px;top:71px;font-size:8.2px;font-weight:700;letter-spacing:1.1px}
.cta-button{position:absolute;left:310px;top:99px;width:96px;height:25px;border:1.5px solid #fff;border-radius:2px;font-size:8.2px;font-weight:700;line-height:22px}

/* footer */
.site-footer{left:0;top:1034px;width:715px;height:136px;background:linear-gradient(#1f1f1f,#171717);color:#fff}
.footer-heading{position:absolute;top:27px;font-size:8.8px}
.footer-divider{position:absolute;top:24px;width:1px;height:94px;background:#3a3a3a}
.social-tile{position:absolute;top:51px;width:43px;height:55px;text-align:center}
.social-tile .dot{position:absolute;left:10px;top:6px;width:23px;height:23px;border-radius:50%;background:rgba(255,255,255,.18)}
.social-tile .count{position:absolute;left:0;width:43px;top:40px;font-size:7.2px}
.tile-a{left:58px;background:var(--fb)}
.tile-b{left:106px;background:var(--tw)}
.tile-c{left:154px;background:var(--gp)}
.mailing-text{position:absolute;left:319px;top:52px;width:150px;font-size:6.4px;line-height:11px;color:#aaa}
.mail-input{position:absolute;left:319px;top:77px;width:119px;height:17px;background:#f3f3f3;font-size:6px;color:#999;padding:5px 0 0 10px}
.mail-submit{position:absolute;left:438px;top:77px;width:19px;height:17px;background:var(--orange)}
.mail-submit svg{position:absolute;left:5px;top:4px;width:9px;height:9px}
.mail-note{position:absolute;left:319px;top:100px;font-size:6.2px;color:#888}
.footer-menu{position:absolute;left:579px;top:52px;list-style:none}
.footer-menu li{font-size:6.8px;line-height:12.9px;color:#fff}

.bottom-bar{left:0;top:1170px;width:715px;height:30px;background:var(--bottom-bg);text-align:center;font-size:6.4px;color:#777;padding-top:12px}
</style>
</head>
<body>

<header class="site-header">
  <div class="abs brand-name">Halvik.</div>
  <div class="abs brand-tagline">Leadership toolkit for firms on the rise</div>
  <nav class="main-nav">
    <a style="left:366px">Home</a>
    <a style="left:427px">About Us</a>
    <a class="active" style="left:494px">Services</a>
    <a style="left:565px">Gallery</a>
    <a style="left:623px">Contact Us</a>
  </nav>
  <div class="abs nav-underline"></div>
</header>

<div class="abs breadcrumb">Home <span class="sep">&gt;&gt;</span> <span class="current">Services</span></div>

<h1 class="abs section-title">Our Services</h1>
<p class="abs section-intro">Donec eu viverra odio, eu cursus orci. Vestibulum id imperdiet est, non dictum leo. Aenean dictum nunc ex, quis vehicula dolor posuere id. Donec luctus luctus nisl, id porta turpis. Class aptent taciti sociosqu ad litora torquent per conubia nostra, per inceptos himenaeos. Curabitur metus libero, suscipit pretium erat sed, cursus faucibus erat. Vestibulum ante ipsum primis in</p>

<article class="service-card" style="top:251px">
  <div class="service-icon">
    <svg viewBox="0 0 40 40" fill="#fff"><rect x="4" y="6" width="2" height="28"/><rect x="4" y="32" width="32" height="2"/><rect x="10" y="20" width="4" height="10"/><rect x="16" y="16" width="4" height="14"/><rect x="22" y="22" width="4" height="8"/><rect x="28" y="12" width="4" height="18"/></svg>
  </div>
  <h2 class="service-title">Growth Management</h2>
  <p class="service-text">In varius venenatis elit, a placerat lacus. Mauris suscipit hendrerit ante, non ullamcorper erat vehicula a. Nullam sodales sem eros. Vestibulum vehicula egestas tincidunt. Phasellus gravida nulla ac mollis tempus. Morbi vitae suscipit tellus, id sodales dolor. Lorem ipsum dolor sit amet, consectetur adipiscing elit. Mauris consectetur lorem dapibus metus porttitor, quis gravida ligula aliquam. Nulla lacinia rutrum enim, sit amet scelerisque nibh pharetra in. Suspendisse iaculis velit sapien, et accumsan erat auctor sit amet. In at nulla eu mauris iaculis semper. Donec scelerisque ligula eu lacus venenatis, ac viverra lectus aliquet. Donec efficitur nisi mi, eget blandit sapien fringilla id. Etiam vehicula, nisl et porta accumsan, velit lacus eleifend sapien, eu molestie nulla arcu vel dui. Nam quis posuere lorem. Morbi nec posuere ligula.</p>
</article>

<article class="service-card" style="top:394px">
  <div class="service-icon">
    <svg viewBox="0 0 40 40" fill="none" stroke="#fff" stroke-width="2.4"><path d="M20 7a8 8 0 0 0-5 14.5c1.3 1 1.6 2.2 1.6 3.5h6.8c0-1.3.3-2.5 1.6-3.5A8 8 0 0 0 20 7z"/><path d="M16.6 28h6.8M17.5 31.5h5" /><path d="M16 13a5 5 0 0 1 3-2" stroke-width="1.6"/></svg>
  </div>
  <h2 class="service-title">Corporate Communication</h2>
  <p class="service-text">In varius venenatis elit, a placerat lacus. Mauris suscipit hendrerit ante, non ullamcorper erat vehicula a. Nullam sodales sem eros. Vestibulum vehicula egestas tincidunt. Phasellus gravida nulla ac mollis tempus. Morbi vitae suscipit tellus, id sodales dolor. Lorem ipsum dolor sit amet, consectetur adipiscing elit. Mauris consectetur lorem dapibus metus porttitor, quis gravida ligula aliquam. Nulla lacinia rutrum enim, sit amet scelerisque nibh pharetra in. Suspendisse iaculis velit sapien, et accumsan erat auctor sit amet. In at nulla eu mauris iaculis semper. Donec scelerisque ligula eu lacus venenatis, ac viverra lectus aliquet. Donec efficitur nisi mi, eget blandit sapien fringilla id. Etiam vehicula, nisl et porta accumsan, velit lacus eleifend sapien, eu molestie nulla arcu vel dui.</p>
</article>

<article class="service-card" style="top:537px">
  <div class="service-icon">
    <svg viewBox="0 0 40 40" fill="none" stroke="#fff" stroke-width="2"><rect x="5" y="8" width="30" height="27" rx="2"/><path d="M5 15h30M11.5 15v20M17.5 15v20M23.5 15v20M29.5 15v20M5 21.5h30M5 28h30"/><path d="M12 4v7M28 4v7" stroke-width="3"/></svg>
  </div>
  <h2 class="service-title">Project Management</h2>
  <p class="service-text">In varius venenatis elit, a placerat lacus. Mauris suscipit hendrerit ante, non ullamcorper erat vehicula a. Nullam sodales sem eros. Vestibulum vehicula egestas tincidunt. Phasellus gravida nulla ac mollis tempus. Morbi vitae suscipit tellus, id sodales dolor. Lorem ipsum dolor sit amet, consectetur adipiscing elit. Mauris consectetur lorem dapibus metus porttitor, quis gravida ligula aliquam. Nulla lacinia rutrum enim, sit amet scelerisque nibh pharetra in. Suspendisse iaculis velit sapien, et accumsan erat auctor sit amet. In at nulla eu mauris iaculis semper. Donec scelerisque ligula eu lacus venenatis, ac viverra lectus aliquet.</p>
</article>

<article class="service-card" style="top:680px">
  <div class="service-icon">
    <svg viewBox="0 0 40 40" fill="none" stroke="#fff" stroke-width="2.2" stroke-linejoin="round"><rect x="4" y="19" width="6" height="12" fill="#fff"/><path d="M10 20l6-5 4-6c1.5-1 3 0 2.5 2L21 16h13a2.5 2.5 0 0 1 0 5h-6M28 21a2.3 2.3 0 0 1 0 4.5h-2M26 25.5a2.2 2.2 0 0 1 0 4.3h-2M24 29.8a2 2 0 0 1 0 4H14l-4-3"/></svg>
  </div>
  <h2 class="service-title">Concepetualizing</h2>
  <p class="service-text">In varius venenatis elit, a placerat lacus. Mauris suscipit hendrerit ante, non ullamcorper erat vehicula a. Nullam sodales sem eros. Vestibulum vehicula egestas tincidunt. Phasellus gravida nulla ac mollis tempus. Morbi vitae suscipit tellus, id sodales dolor. Lorem ipsum dolor sit amet, consectetur adipiscing elit. Mauris consectetur lorem dapibus metus porttitor, quis gravida ligula aliquam. Nulla lacinia rutrum enim, sit amet scelerisque nibh pharetra in.</p>
</article>

<section class="abs cta">
  <h2 class="cta-heading">DONEC EU VIVERRA ODIO, EU CURSUS ORCI.</h2>
  <p class="cta-sub">IN VARIUS VENENATIS ELIT, A PLACERAT LACUS. MAURIS SUSCIPIT</p>
  <div class="cta-button">CONTACT NOW</div>
</section>

<footer class="abs site-footer">
  <h3 class="footer-heading" style="left:58px;font-weight:400">Let's Connect</h3>
  <div class="social-tile tile-a"><span class="dot"></span><span class="count">2598</span></div>
  <div class="social-tile tile-b"><span class="dot"></span><span class="count">4576</span></div>
  <div class="social-tile tile-c"><span class="dot"></span><span class="count">1269</span></div>

  <div class="footer-divider" style="left:261px"></div>

  <h3 class="footer-heading" style="left:318px;font-weight:400">Mailing List</h3>
  <p class="mailing-text">Sign up for our mailing list to get latest updates and offers.</p>
  <div class="mail-input">Email address</div>
  <div class="mail-submit"><svg viewBox="0 0 10 10" fill="none" stroke="#fff" stroke-width="2"><path d="M1 5l3 3 5-6"/></svg></div>
  <p class="mail-note">We respect your privacy</p>

  <div class="footer-divider" style="left:521px"></div>

  <h3 class="footer-heading" style="left:579px;font-weight:400">Menu</h3>
  <ul class="footer-menu">
    <li>Home</li><li>About Us</li><li>Services</li><li>Gallery</li><li>Contact Us</li>
  </ul>
</footer>

<div class="abs bottom-bar">© Copyrights 2015 All Rights Reserved</div>

</body>
</html>
```